Business card for medical clinic

I need an upmarket, modern medical/health business card for my clinic

Contact Information for Business Card

name, address, email, qr code

```html
<!DOCTYPE html>
<html lang="en">
<head>
<meta charset="utf-8">
<title>Brightmere Clinic – Business Card</title>
<link href="https://fonts.googleapis.com/css2?family=Cinzel:wght@500&family=Arimo:wght@400&display=swap" rel="stylesheet">
<style>
  :root {
    --page-bg: #e9ecef;
    --card-white: #ffffff;
    --navy: #1a2d55;
    --blue-mid: #0f5f97;
    --blue-bright: #1fb4ea;
    --brand-ink: #1f5a8a;
    --brand-ink-light: #8fd8f7;
    --name-ink: #1d4873;
    --muted: #9aa3ad;
    --silver: #c9ced4;
    --contact-ink: #ffffff;
  }
  * { box-sizing: border-box; margin: 0; padding: 0; }
  html, body { width: 1200px; height: 874px; overflow: hidden; }
  body {
    background: var(--page-bg);
    display: flex;
    align-items: center;
    justify-content: center;
    gap: 40px;
  }
  .card {
    position: relative;
    width: 540px;
    height: 310px;
    border-radius: 16px;
    overflow: hidden;
    box-shadow: 0 6px 18px rgba(20, 30, 50, 0.18);
  }
  /* Front */
  .card-front { background: var(--card-white); }
  .card-front .wave { position: absolute; inset: 0; width: 100%; height: 100%; }
  .brand-name {
    font-family: 'Arimo', sans-serif;
    font-weight: 400;
    color: var(--brand-ink);
  }
  .card-front .brand-name {
    position: absolute;
    top: 44px;
    left: 34px;
    font-size: 24px;
  }
  .person {
    position: absolute;
    top: 106px;
    left: 46px;
  }
  .person-name {
    font-family: 'Cinzel', serif;
    font-weight: 500;
    font-size: 23px;
    color: var(--name-ink);
    letter-spacing: 1px;
  }
  .person-role {
    font-family: 'Arimo', sans-serif;
    font-size: 12px;
    color: var(--muted);
    margin-top: -2px;
  }
  .contacts {
    position: absolute;
    right: 22px;
    bottom: 20px;
    list-style: none;
    font-family: 'Arimo', sans-serif;
    font-size: 13.5px;
    line-height: 17.5px;
    color: var(--contact-ink);
    text-align: right;
  }
  .contacts li { display: flex; justify-content: flex-end; align-items: center; gap: 8px; }
  .contacts .icon { width: 12px; height: 12px; flex: none; }
  .contacts .no-icon { padding-right: 20px; }
  /* Back */
  .card-back {
    background: radial-gradient(ellipse 60% 70% at 50% 45%, var(--blue-bright) 0%, var(--blue-mid) 45%, var(--navy) 100%);
    display: flex;
    align-items: center;
    justify-content: center;
  }
  .card-back .brand-name {
    font-size: 38px;
    color: var(--brand-ink-light);
  }
</style>
</head>
<body>

  <section class="card card-front" aria-label="Business card front">
    <svg class="wave" viewBox="0 0 540 310" preserveAspectRatio="none" aria-hidden="true">
      <defs>
        <linearGradient id="bandFill" x1="0" y1="0" x2="1" y2="0.3">
          <stop offset="0" stop-color="#1a2d55"/>
          <stop offset="0.55" stop-color="#0f7fb8"/>
          <stop offset="1" stop-color="#1a2d55"/>
        </linearGradient>
      </defs>
      <path d="M0,160 C120,232 400,222 540,8 L540,310 L0,310 Z" fill="var(--silver)"/>
      <path d="M0,170 C120,242 400,232 540,20 L540,310 L0,310 Z" fill="url(#bandFill)"/>
    </svg>

    <p class="brand-name">Brightmere Clinic</p>

    <div class="person">
      <p class="person-name">Daniel Reeve</p>
      <p class="person-role">President</p>
    </div>

    <ul class="contacts">
      <li>555-210-4817
        <svg class="icon" viewBox="0 0 12 12" aria-hidden="true"><path d="M2.5 1 L4.5 1 L5 3.5 L3.8 4.4 C4.5 6 6 7.5 7.6 8.2 L8.5 7 L11 7.5 L11 9.5 C11 10.3 10.3 11 9.5 11 C5 11 1 7 1 2.5 C1 1.7 1.7 1 2.5 1 Z" fill="#fff"/></svg>
      </li>
      <li>555-382-9063
        <svg class="icon" viewBox="0 0 12 12" aria-hidden="true"><rect x="3" y="0.8" width="6" height="10.4" rx="1" fill="none" stroke="#fff" stroke-width="1.2"/><circle cx="6" cy="9.4" r="0.6" fill="#fff"/></svg>
      </li>
      <li>info@brightmereclinic.com
        <svg class="icon" viewBox="0 0 12 12" aria-hidden="true"><rect x="0.5" y="2.5" width="11" height="7.5" fill="#fff"/><path d="M0.8 2.8 L6 6.8 L11.2 2.8" fill="none" stroke="#1a2d55" stroke-width="1"/></svg>
      </li>
      <li>www.brightmereclinic.com
        <svg class="icon" viewBox="0 0 12 12" aria-hidden="true"><circle cx="6" cy="6" r="5.3" fill="#fff"/><path d="M1 6 H11 M6 0.8 C3.5 3.5 3.5 8.5 6 11.2 M6 0.8 C8.5 3.5 8.5 8.5 6 11.2" fill="none" stroke="#1a2d55" stroke-width="0.8"/></svg>
      </li>
      <li class="no-icon">412 Alder Court</li>
      <li class="no-icon">Fairview, Canada 20817</li>
    </ul>
  </section>

  <section class="card card-back" aria-label="Business card back">
    <p class="brand-name">Brightmere Clinic</p>
  </section>

</body>
</html>
```